Accounting firm needing business card / letterhead designed
Marcus L. Trenholm, CPA
marcus@veltrowledger.com
www.veltrowledger.com
842 E Alder Ave Halden Falls, MN 43827
612-562-0974

```html
<!DOCTYPE html>
<html lang="en">
<head>
<meta charset="utf-8">
<title>Veltro Ledger — Business Card</title>
<link rel="stylesheet" href="https://fonts.googleapis.com/css2?family=Aldrich&family=Roboto:wght@400&display=swap">
<style>
  :root {
    --stage: #1d1d1f;
    --navy: #2a2467;
    --violet-light: #453ba8;
    --violet-dark: #241e62;
    --lime: #8dc63f;
    --paper-light: #f9f9f9;
    --paper-dark: #e8e8e8;
    --ink: #4a4a4a;
    --white: #ffffff;
  }
  * { box-sizing: border-box; margin: 0; padding: 0; }
  html, body {
    width: 1200px; height: 960px; overflow: hidden;
    background: var(--stage);
  }
  .canvas { position: relative; width: 1200px; height: 960px; }

  .card {
    position: absolute;
    width: 600px; height: 342px;
    border-radius: 22px;
    overflow: hidden;
    box-shadow: 0 4px 10px rgba(0,0,0,0.5);
  }
  .card--front {
    left: 302px; top: 129px;
    background: linear-gradient(120deg, var(--paper-light), var(--paper-dark));
  }
  .card--back {
    left: 299px; top: 488px; height: 343px;
    background: linear-gradient(150deg, var(--violet-light) 0%, var(--violet-dark) 45%, var(--violet-dark) 100%);
  }

  .brand-name {
    position: absolute;
    font-family: "Aldrich", sans-serif;
    font-weight: 400;
    letter-spacing: 3px;
    white-space: nowrap;
  }
  .card--front .brand-name {
    right: 36px; top: 64px;
    font-size: 36px;
    line-height: 1;
    color: var(--navy);
  }
  .card--back .brand-name {
    left: 0; right: 0; top: 140px;
    text-align: center;
    font-size: 48px;
    line-height: 1;
    color: var(--white);
  }

  .holder-name {
    position: absolute;
    left: 33px; top: 210px;
    font-family: "Aldrich", sans-serif;
    font-weight: 400;
    font-size: 22px;
    line-height: 1;
    letter-spacing: 0.5px;
    color: var(--navy);
    text-transform: uppercase;
  }
  .rule {
    position: absolute;
    left: 33px; top: 246px;
    width: 530px; height: 2px;
    background: var(--lime);
  }

  .contact-list {
    position: absolute;
    left: 33px; top: 258px;
    list-style: none;
    font-family: "Roboto", sans-serif;
    font-size: 14px;
    line-height: 19px;
    color: var(--ink);
  }
  .contact-list li { display: flex; align-items: center; gap: 8px; }
  .contact-list svg { width: 13px; height: 13px; fill: var(--navy); flex: none; }

  .address {
    position: absolute;
    right: 37px; top: 277px;
    font-family: "Roboto", sans-serif;
    font-style: normal;
    font-size: 14px;
    line-height: 19px;
    color: var(--ink);
    text-align: right;
  }
</style>
</head>
<body>
<main class="canvas">
  <section class="card card--front" aria-label="Card front">
    <div class="brand-name">VELTRO LEDGER</div>
    <h1 class="holder-name">Marcus L. Trenholm, CPA</h1>
    <div class="rule"></div>
    <ul class="contact-list">
      <li>
        <svg viewBox="0 0 24 24" aria-hidden="true"><path d="M6.6 10.8a15.1 15.1 0 0 0 6.6 6.6l2.2-2.2c.3-.3.7-.4 1-.2 1.1.4 2.3.6 3.6.6.6 0 1 .4 1 1V20c0 .6-.4 1-1 1A17 17 0 0 1 3 4c0-.6.4-1 1-1h3.5c.6 0 1 .4 1 1 0 1.3.2 2.5.6 3.6.1.3 0 .7-.2 1L6.6 10.8z"/></svg>
        <span>612-562-0974</span>
      </li>
      <li>
        <svg viewBox="0 0 24 24" aria-hidden="true"><path d="M2 5h20v14H2z M2 5l10 8 10-8" fill="none" stroke="#2a2467" stroke-width="2.4"/><path d="M3 6h18l-9 7z"/></svg>
        <span>marcus@veltrowledger.com</span>
      </li>
      <li>
        <svg viewBox="0 0 24 24" aria-hidden="true"><circle cx="12" cy="12" r="10"/><path d="M2 12h20M12 2c3 3 3 17 0 20M12 2c-3 3-3 17 0 20" fill="none" stroke="#f2f2f2" stroke-width="1.6"/></svg>
        <span>www.veltrowledger.com</span>
      </li>
    </ul>
    <address class="address">842 E Alder Ave<br>Halden Falls, MN 43827</address>
  </section>

  <section class="card card--back" aria-label="Card back">
    <div class="brand-name">VELTRO LEDGER</div>
  </section>
</main>
</body>
</html>
```